Real Estate Company / Capital Needs Cards!

need business cards designed using the logos that were just designed by pixelbarn.

Reason: per designers request deadline extended 1 day…thank you.

Target Market(s)

Investors and clients looking to purchase real estate or invest in the business.

Industry/Entity Type

Business

Requirements
Must have
• two designs - one for the real estate logo and one for the capital logo, similar but slightly different.
Nice to have
• something to make it pop (perhaps on the back)
Should not have
• much color

```html
<!DOCTYPE html>
<html lang="en">
<head>
<meta charset="utf-8">
<title>Marlow Real Estate – Business Cards</title>
<link rel="stylesheet" href="https://fonts.googleapis.com/css2?family=Source+Sans+3:wght@400;600;700&display=swap">
<style>
  :root {
    --backdrop: #e9e7e4;
    --card: #ffffff;
    --panel: #6d6e71;
    --swoosh: #a7a8aa;
    --ink: #6d6e71;
    --ink-dark: #3a3a3c;
    --on-panel: #ffffff;
  }
  * { box-sizing: border-box; margin: 0; padding: 0; }
  html, body { width: 1200px; height: 498px; overflow: hidden; }
  body {
    background: var(--backdrop);
    font-family: "Source Sans 3", sans-serif;
    position: relative;
  }
  .card {
    position: absolute;
    top: 95px;
    width: 540px;
    height: 309px;
    background: var(--card);
    box-shadow: 0 6px 18px rgba(0,0,0,0.18);
    overflow: hidden;
  }
  .card--front { left: 40px; }
  .card--back { left: 620px; }

  .front__shape { position: absolute; inset: 0; }

  .brand {
    position: absolute;
    left: 38px;
    top: 128px;
    display: flex;
    align-items: center;
    gap: 12px;
    color: var(--ink);
  }
  .brand__square { width: 44px; height: 44px; background: var(--swoosh); }
  .brand__name {
    font-size: 24px;
    font-weight: 600;
    letter-spacing: 1px;
    line-height: 1.05;
    text-transform: uppercase;
  }
  .brand__name small { display: block; font-size: 13px; letter-spacing: 3px; }

  .contact {
    position: absolute;
    right: 26px;
    top: 40px;
    text-align: right;
    color: var(--on-panel);
  }
  .contact__name { font-size: 20px; font-weight: 700; line-height: 1.1; }
  .contact__title { font-size: 16px; line-height: 1.2; margin-bottom: 34px; }
  .contact__line {
    display: flex;
    justify-content: flex-end;
    align-items: center;
    gap: 5px;
    font-size: 14.5px;
    line-height: 1.45;
  }
  .contact__line svg { width: 11px; height: 11px; fill: var(--on-panel); flex: none; }
  .contact__address { font-size: 15px; line-height: 1.3; margin-top: 30px; }

  .back__brand {
    position: absolute;
    left: 0; right: 0;
    top: 108px;
    display: flex;
    justify-content: center;
    align-items: center;
    gap: 16px;
    color: var(--ink);
  }
  .back__square { width: 56px; height: 56px; background: var(--swoosh); }
  .back__name {
    font-size: 34px;
    font-weight: 600;
    letter-spacing: 2px;
    text-transform: uppercase;
    line-height: 1;
  }
  .back__name small { display: block; font-size: 16px; letter-spacing: 5px; margin-top: 4px; }
  .back__web {
    position: absolute;
    left: 0; right: 0;
    top: 236px;
    text-align: center;
    font-size: 15px;
    letter-spacing: 2.5px;
    color: var(--ink-dark);
  }
  .back__web strong { font-weight: 700; }
</style>
</head>
<body>
  <section class="card card--front">
    <svg class="front__shape" viewBox="0 0 540 309" aria-hidden="true">
      <path d="M292 0 Q270 200 404 309 H426 Q290 210 300 0 Z" fill="var(--swoosh)"/>
      <path d="M306 0 H540 V309 H432 Q296 210 306 0 Z" fill="var(--panel)"/>
    </svg>

    <div class="brand">
      <span class="brand__square"></span>
      <div class="brand__name">Marlow<small>Real Estate</small></div>
    </div>

    <div class="contact">
      <p class="contact__name">Your Name</p>
      <p class="contact__title">Title</p>
      <p class="contact__line">
        <svg viewBox="0 0 24 24"><path d="M6.6 10.8a15 15 0 0 0 6.6 6.6l2.2-2.2a1 1 0 0 1 1-.25 11.4 11.4 0 0 0 3.6.57 1 1 0 0 1 1 1V20a1 1 0 0 1-1 1A17 17 0 0 1 3 4a1 1 0 0 1 1-1h3.5a1 1 0 0 1 1 1c0 1.25.2 2.45.57 3.57a1 1 0 0 1-.25 1z"/></svg>
        123-456-7980
      </p>
      <p class="contact__line">
        <svg viewBox="0 0 24 24"><circle cx="12" cy="7" r="5"/><path d="M2 23c0-6 4.5-9 10-9s10 3 10 9z"/></svg>
        123-568-7896
      </p>
      <p class="contact__line">
        <svg viewBox="0 0 24 24"><path d="M2 5h20v14H2z M3 6l9 7 9-7" stroke="#6d6e71" stroke-width="1.5"/></svg>
        marlowestate@mailbox.com
      </p>
      <p class="contact__address">Street Name City Name<br>State ZipCode</p>
    </div>
  </section>

  <section class="card card--back">
    <div class="back__brand">
      <span class="back__square"></span>
      <div class="back__name">Marlow<small>Real Estate</small></div>
    </div>
    <p class="back__web">www.<strong>marlowrealestate</strong>.com</p>
  </section>
</body>
</html>
```